Front page of Orthodox Christian Monastery Website

I am attaching a couple of versions of design that was already created for the front page of the website. You can grab the same pictures and titles (do not need to know the Russian language) to create your own version of design.
Background: Monastery website contains sermons, stories about monastery life, monastery music of the sisterhood.
Main principles of the design:
1. Various materials/sermons/music have to be clearly visible immediately to the site visitor.
2. Text descriptions to photos should be using font with a good contrast, highly clickable and easily readable.
3. Every article should have a photo or a quality picture (use those in the sample) that will convey something about it.
4. On the top, there will be a menu, which will be a line of words (just use generic words for now).
5. Design should reflect Christian Orthodox themes and fonts.
Updates

Target Market(s)

Orthodox Christian believers around the world and those that are interested in Orthodox Christianity

Number of Pages Required

1 page

Font styles to use
Serif

Colors

Designer to choose colors to be used in the design.

Requirements
Must have
• In the project description
Nice to have
• for some ideas see a popular Orthodox Christian website:
• www.verenskaya-lampada.ru
• We don't want to copy it, but it could give ideas.
Should not have
• Should not be overly complex

```html
<!DOCTYPE html>
<html lang="en">
<head>
<meta charset="utf-8">
<title>Orthodox Christian Monastery</title>
<link href="https://fonts.googleapis.com/css2?family=Playfair+Display:wght@400;700&family=Open+Sans:wght@400;600&display=swap" rel="stylesheet">
<style>
:root{
  --green:#0c3a20;
  --green-footer:#14502d;
  --orange:#e9a03a;
  --card:#e7e7e7;
  --ink:#1d1d1d;
  --muted:#5c5c5c;
  --white:#ffffff;
  --serif:"Playfair Display", Georgia, serif;
  --sans:"Open Sans", Arial, sans-serif;
}
*{box-sizing:border-box;margin:0;padding:0}
html,body{width:1200px;height:2885px;overflow:hidden;background:var(--white)}
body{position:relative;font-family:var(--sans);color:var(--ink)}
.abs{position:absolute}
.site-title{top:22px;left:0;width:1200px;text-align:center;font-family:var(--serif);font-size:42px;color:var(--green);font-weight:400;letter-spacing:.5px}
.main-nav{top:88px;left:133px;width:934px;height:33px;background:var(--orange);display:flex;align-items:center;padding:0 10px;z-index:2}
.main-nav a{font-family:var(--serif);font-size:11.5px;color:#2b1a05;text-decoration:none;text-transform:uppercase;padding:0 11px;line-height:33px}
.main-nav a.active{background:#d58b22;color:var(--white)}
.main-nav svg{margin-left:auto}
.hero{top:108px;left:0;width:1200px;height:507px;background:linear-gradient(180deg,#5d7fa8 0%,#9fb4c9 35%,#3e4a3a 62%,#1d231c 100%)}
.hero-caption{top:519px;left:0;width:1200px;height:96px;background:rgba(235,235,235,.82);padding:16px 133px 0}
.hero-caption h2{font-family:var(--serif);font-weight:400;font-size:21px;color:#111}
.hero-caption p{font-size:11.5px;line-height:17px;color:#222;margin-top:6px}
.hero-arrow{top:550px}
.tabs{top:660px;left:133px;width:667px;height:62px}
.tab-row{position:absolute;left:0;bottom:0;display:flex;gap:4px}
.tab-row span{font-family:var(--serif);font-size:14px;color:var(--white);background:var(--green);padding:8px 14px;display:block}
.tab-row span.active{background:var(--card);color:var(--green);border-top:3px solid var(--green)}
.article{left:133px;width:667px;height:160px;background:var(--card);display:flex;padding:7px}
.article .photo{width:204px;height:146px;flex:none}
.article .body{padding:8px 12px 0 16px}
.article time{font-family:var(--serif);font-size:12px;color:#111}
.article h3{font-family:var(--sans);font-weight:400;font-size:13.5px;line-height:18px;margin-top:10px;color:#111}
.article p{font-size:9.6px;line-height:15px;color:var(--muted);margin-top:8px}
.btn-outline{display:inline-block;font-family:var(--serif);font-size:11.5px;border:1px solid var(--green);color:var(--green);padding:6px 14px;background:var(--white)}
.btn-light{display:inline-block;font-family:var(--serif);font-size:11.5px;border:1px solid #c9d3cc;color:var(--white);padding:6px 16px}
.panel{background:var(--green);color:var(--white)}
.panel-top{position:absolute;left:0;top:-14px}
.panel h2{font-family:var(--serif);font-weight:400;font-size:20px;text-align:center}
.side-item{position:absolute;left:12px;width:220px;height:92px;background:var(--card);display:flex;padding:7px;color:var(--ink)}
.side-item .photo{width:78px;height:78px;flex:none}
.side-item .txt{padding-left:10px;padding-top:2px}
.side-item time{font-family:var(--serif);font-size:11px}
.side-item p{font-size:9px;line-height:13px;color:var(--muted);margin-top:5px}
.video-card{position:absolute;top:72px;width:152px;height:216px;background:var(--white);color:var(--ink)}
.video-card .photo{height:120px;display:flex;align-items:center;justify-content:center}
.video-card time{display:block;font-family:var(--serif);font-size:12px;padding:12px 12px 0}
.video-card p{font-size:9.5px;line-height:14px;color:var(--muted);padding:6px 12px 0}
.gallery-title{top:2242px;left:0;width:1200px;display:flex;justify-content:center;align-items:center;gap:22px;font-family:var(--serif);font-size:22px;color:var(--green)}
.gallery-nav{width:22px;height:22px;border:1px solid #999;display:flex;align-items:center;justify-content:center}
.gallery{top:2288px;left:0;width:1200px;height:164px;display:flex;gap:3px}
.gallery div{flex:1}
.footer{top:2452px;left:0;width:1200px;height:433px;background:linear-gradient(180deg,#16552f,#0f4324);color:var(--white)}
.footer h2{font-family:var(--serif);font-weight:400;font-size:21px;text-align:center;position:absolute;top:58px;width:1200px;letter-spacing:.5px}
.subscribe{position:absolute;top:96px;left:421px;width:367px;height:42px;background:var(--white);display:flex;align-items:center;padding:0 14px;color:#333;font-size:11.5px}
.subscribe svg{margin-left:auto}
.rule{position:absolute;left:133px;width:934px;height:1px;background:rgba(255,255,255,.25)}
.fcol{position:absolute;top:188px}
.fcol h3{font-family:var(--serif);font-weight:400;font-size:16px}
.fcol ul{list-style:none;margin-top:14px}
.fcol li{font-size:10.5px;line-height:24px;color:#dfe8e2}
.fcol li::before{content:"•";color:var(--orange);margin-right:7px}
.social{display:flex;gap:6px;margin-top:14px}
.social span{width:24px;height:24px;border-radius:50%;display:block}
.copyright{position:absolute;top:2806px;left:0;width:1200px;text-align:center;font-size:11px;color:#dfe8e2;letter-spacing:.3px}
</style>
</head>
<body>

<h1 class="abs site-title">Orthodox Christian Monastery</h1>

<nav class="abs main-nav">
  <a class="active">Home</a><a>About Us</a><a>Evetns</a><a>Media</a><a>Community</a><a>Forum</a><a>Support</a><a>Seminars</a><a>Newsletter</a><a>Search</a>
  <svg width="14" height="14" viewBox="0 0 14 14"><circle cx="6" cy="6" r="4.2" fill="none" stroke="#2b1a05" stroke-width="1.8"/><line x1="9" y1="9" x2="13" y2="13" stroke="#2b1a05" stroke-width="2"/></svg>
</nav>

<div class="abs hero" role="img" aria-label="Photograph of a white monastery church with dark domes and golden cupolas under a blue sky"></div>
<div class="abs hero-caption">
  <h2>Nullam lorem urna, tempus eget mollis et, dapibus</h2>
  <p>Suspendisse gravida ornare erat sed pulvinar. Vestibulum luctus ex in egestas fringilla. Fusce nec leo ac urna pulvinar auctor. Mauris bibendum fringilla velit. Nulla in lorem massa<br>pellentesque posuere. Nulla tristique posuere molestie. Aliquam erat volutpat.</p>
</div>
<svg class="abs hero-arrow" style="left:42px" width="20" height="30" viewBox="0 0 20 30"><polyline points="16,3 5,15 16,27" fill="none" stroke="#555" stroke-width="3"/></svg>
<svg class="abs hero-arrow" style="left:1138px" width="20" height="30" viewBox="0 0 20 30"><polyline points="4,3 15,15 4,27" fill="none" stroke="#555" stroke-width="3"/></svg>

<!-- Tabs -->
<div class="abs tabs">
  <svg class="abs" style="left:0;top:0" width="667" height="62" viewBox="0 0 667 62"><polygon points="0,18 667,0 667,14 0,28" fill="var(--orange)"/><polygon points="0,28 667,14 667,62 0,62" fill="var(--green)"/></svg>
  <div class="tab-row"><span class="active">About Monastery Life</span><span>Monastery Music of the Sisterhood</span><span>Sermons</span></div>
</div>

<article class="abs article" style="top:727px">
  <div class="photo" role="img" aria-label="Photo of a priest in red vestments blessing the faithful" style="background:linear-gradient(135deg,#b8453a,#6d4a3a 60%,#d9cbb5)"></div>
  <div class="body"><time>4 May, 2018</time><h3>Pellentesque blandit lacus eget nunc faucibus, tincidunt eros viverra. Phasellus consequat sagittis nisi suscipit feugiat.</h3><p>Cras eget leo sed nunc hendrerit ultricies eu at nisl. Praesent iaculis faucibus urna sit amet lacinia. Maecenas consequat justo enim, ac mattis massa imperdiet quis. Fusce eget neque elit. Sed augue orci, elementum in magna congue, tincidunt vulputate erat. Aliquam consectetur orci molestie dictum molestie. Proin eget congue nulla, vel tempor diam.</p></div>
</article>
<article class="abs article" style="top:902px">
  <div class="photo" role="img" aria-label="Photo of nuns in black habits gathered with flowers" style="background:linear-gradient(135deg,#3a3a3a,#171717 55%,#8a8a8a)"></div>
  <div class="body"><time>4 May, 2018</time><h3>Vestibulum condimentum, risus ut posuere cursus, velit justo accumsan sem, lobortis aliquet metus dui eu libero.</h3><p>Cras eget leo sed nunc hendrerit ultricies eu at nisl. Praesent iaculis faucibus urna sit amet lacinia. Maecenas consequat justo enim, ac mattis massa imperdiet quis. Fusce eget neque elit. Sed augue orci, elementum in magna congue, tincidunt vulputate erat. Aliquam consectetur orci molestie dictum molestie. Proin eget congue nulla, vel tempor diam.</p></div>
</article>
<article class="abs article" style="top:1077px">
  <div class="photo" role="img" aria-label="Photo of a nun speaking on a stage under blue light" style="background:linear-gradient(135deg,#1c2a8a,#0d1240 60%,#2b3fb0)"></div>
  <div class="body"><time>4 May, 2018</time><h3>Fusce sollicitudin lorem et luctus volutpat. Proin placerat dapibus gravida. In tristique tristique nulla eget hendrerit.</h3><p>Cras eget leo sed nunc hendrerit ultricies eu at nisl. Praesent iaculis faucibus urna sit amet lacinia. Maecenas consequat justo enim, ac mattis massa imperdiet quis. Fusce eget neque elit. Sed augue orci, elementum in magna congue, tincidunt vulputate erat. Aliquam consectetur orci molestie dictum molestie. Proin eget congue nulla, vel tempor diam.</p></div>
</article>
<article class="abs article" style="top:1252px">
  <div class="photo" role="img" aria-label="Concert poster for the sisterhood choir on a dark background" style="background:linear-gradient(180deg,#2a2a2a,#111 70%,#3a3a3a)"></div>
  <div class="body"><time>4 May, 2018</time><h3>Maecenas vel tortor accumsan quam varius imperdiet vel eget elit. Aenean facilisis tincidunt lectus, id dictum nisi luctus eget.</h3><p>Cras eget leo sed nunc hendrerit ultricies eu at nisl. Praesent iaculis faucibus urna sit amet lacinia. Maecenas consequat justo enim, ac mattis massa imperdiet quis. Fusce eget neque elit. Sed augue orci, elementum in magna congue, tincidunt vulputate erat. Aliquam consectetur orci molestie dictum molestie. Proin eget congue nulla, vel tempor diam.</p></div>
</article>
<article class="abs article" style="top:1427px">
  <div class="photo" role="img" aria-label="Illustration of a priest with a pen beside a green panel" style="background:linear-gradient(90deg,#e9e9e9 0%,#cfcfcf 45%,#2f8a3e 80%)"></div>
  <div class="body"><time>4 May, 2018</time><h3>Sed tellus ex, imperdiet eget gravida sit amet, volutpat eget turpis. In nec ultricies est. Etiam mattis augue vehicula odio posuere</h3><p>Cras eget leo sed nunc hendrerit ultricies eu at nisl. Praesent iaculis faucibus urna sit amet lacinia. Maecenas consequat justo enim, ac mattis massa imperdiet quis. Fusce eget neque elit. Sed augue orci, elementum in magna congue, tincidunt vulputate erat. Aliquam consectetur orci molestie dictum molestie. Proin eget congue nulla, vel tempor diam.</p></div>
</article>

<a class="abs btn-outline" style="top:1612px;left:133px">View More</a>

<!-- Videos -->
<section class="abs panel" style="top:1687px;left:133px;width:667px;height:351px">
  <svg class="panel-top" width="667" height="28" viewBox="0 0 667 28"><polygon points="0,14 667,0 667,12 0,26" fill="var(--orange)"/><polygon points="0,26 667,12 667,28 0,28" fill="var(--green)"/></svg>
  <h2 style="padding-top:16px">Videos</h2>
  <div class="video-card" style="left:15px"><div class="photo" role="img" aria-label="Video still of a city skyline at dusk" style="background:linear-gradient(180deg,#2c4a8a,#a37c4a)"><svg width="28" height="28" viewBox="0 0 28 28"><circle cx="14" cy="14" r="13" fill="#fff"/><polygon points="11,8 20,14 11,20" fill="#111"/></svg></div><time>4 May, 2018</time><p>Etiam elementum, bibendum feugiat massa. Curabitur venenatis .</p></div>
  <div class="video-card" style="left:176px"><div class="photo" role="img" aria-label="Video still of a painted church fresco" style="background:linear-gradient(135deg,#b06a3a,#6e4a2a 60%,#c9a06a)"><svg width="28" height="28" viewBox="0 0 28 28"><circle cx="14" cy="14" r="13" fill="#fff"/><polygon points="11,8 20,14 11,20" fill="#111"/></svg></div><time>4 May, 2018</time><p>Etiam elementum, bibendum feugiat massa. Curabitur venenatis .</p></div>
  <div class="video-card" style="left:337px"><div class="photo" role="img" aria-label="Video still of a framed icon on a wall" style="background:linear-gradient(135deg,#c8c8c8,#6a6a6a)"><svg width="28" height="28" viewBox="0 0 28 28"><circle cx="14" cy="14" r="13" fill="#fff"/><polygon points="11,8 20,14 11,20" fill="#111"/></svg></div><time>4 May, 2018</time><p>Etiam elementum, bibendum feugiat massa. Curabitur venenatis .</p></div>
  <div class="video-card" style="left:498px"><div class="photo" role="img" aria-label="Video still of sisters at a dining table" style="background:linear-gradient(135deg,#8a5a3a,#3a2a20 60%,#b88a5a)"><svg width="28" height="28" viewBox="0 0 28 28"><circle cx="14" cy="14" r="13" fill="#fff"/><polygon points="11,8 20,14 11,20" fill="#111"/></svg></div><time>4 May, 2018</time><p>Etiam elementum, bibendum feugiat massa. Curabitur venenatis .</p></div>
  <a class="abs btn-light" style="top:294px;left:292px">View All</a>
</section>

<!-- Audios -->
<section class="abs panel" style="top:2067px;left:133px;width:667px;height:121px">
  <h2 style="padding-top:10px;font-size:19px">Audios</h2>
  <p style="text-align:center;font-size:9.5px;color:#cfdcd4;margin-top:2px">Proin a dolor mauris. Vestibulum ante ipsum primis in faucibus orci luctus et ultrices posuere cubilia Curae; Vestibulum eget nisl metus.</p>
  <div class="abs" style="left:0;top:64px;width:667px;height:57px;background:#0a2c18"></div>
  <svg class="abs" style="left:12px;top:74px" width="640" height="38" viewBox="0 0 640 38">
    <circle cx="18" cy="19" r="17" fill="#fff"/><polygon points="13,10 27,19 13,28" fill="#0a2c18"/>
    <rect x="46" y="17" width="490" height="4" fill="#3f5a48"/><rect x="46" y="17" width="210" height="4" fill="var(--orange)"/>
    <polygon points="556,12 564,19 556,26" fill="#fff"/><polygon points="564,12 572,19 564,26" fill="#fff"/><rect x="574" y="12" width="3" height="14" fill="#fff"/>
    <polygon points="606,15 611,15 617,10 617,28 611,23 606,23" fill="#fff"/><path d="M621 14 q4 5 0 10" fill="none" stroke="#fff" stroke-width="2"/>
  </svg>
</section>

<!-- Events -->
<section class="abs panel" style="top:674px;left:823px;width:244px;height:513px">
  <svg class="panel-top" width="244" height="28" viewBox="0 0 244 28"><polygon points="0,14 244,0 244,12 0,26" fill="var(--orange)"/><polygon points="0,26 244,12 244,28 0,28" fill="var(--green)"/></svg>
  <h2 style="padding-top:10px">Events</h2>
  <div class="side-item" style="top:48px"><div class="photo" role="img" aria-label="Photo of a monastery under an evening sky" style="background:linear-gradient(180deg,#1f3c9a,#7a8ab0)"></div><div class="txt"><time>4 May, 2018</time><p>Duis ornare erat eget magna dapibus, in accumsan quam pharetra.</p></div></div>
  <div class="side-item" style="top:152px"><div class="photo" role="img" aria-label="Photo of a priest in red vestments" style="background:linear-gradient(135deg,#c0392b,#7a2a1a)"></div><div class="txt"><time>4 May, 2018</time><p>Duis ornare erat eget magna dapibus, in accumsan quam pharetra.</p></div></div>
  <div class="side-item" style="top:256px"><div class="photo" role="img" aria-label="Photo of a procession outdoors" style="background:linear-gradient(135deg,#8a6a4a,#3a3a2a)"></div><div class="txt"><time>4 May, 2018</time><p>Duis ornare erat eget magna dapibus, in accumsan quam pharetra.</p></div></div>
  <div class="side-item" style="top:360px"><div class="photo" role="img" aria-label="Photo of a church by water at sunset" style="background:linear-gradient(180deg,#5a6a9a,#c98a6a 55%,#2a3a2a)"></div><div class="txt"><time>4 May, 2018</time><p>Duis ornare erat eget magna dapibus, in accumsan quam pharetra.</p></div></div>
  <a class="abs btn-light" style="top:483px;left:81px">View More</a>
</section>

<!-- Seminars -->
<section class="abs panel" style="top:1226px;left:823px;width:244px;height:515px">
  <svg class="panel-top" width="244" height="28" viewBox="0 0 244 28"><polygon points="0,14 244,0 244,12 0,26" fill="var(--orange)"/><polygon points="0,26 244,12 244,28 0,28" fill="var(--green)"/></svg>
  <h2 style="padding-top:10px">Seminars</h2>
  <div class="side-item" style="top:50px"><div class="photo" role="img" aria-label="Portrait of an elder monk" style="background:linear-gradient(135deg,#8a8a8a,#2a2a2a)"></div><div class="txt"><time>4 May, 2018</time><p>Duis ornare erat eget magna dapibus, in accumsan quam pharetra.</p></div></div>
  <div class="side-item" style="top:154px"><div class="photo" role="img" aria-label="Photo of a church service" style="background:linear-gradient(135deg,#6a3a4a,#2a1a2a)"></div><div class="txt"><time>4 May, 2018</time><p>Duis ornare erat eget magna dapibus, in accumsan quam pharetra.</p></div></div>
  <div class="side-item" style="top:258px"><div class="photo" role="img" aria-label="Photo of a white church under blue sky" style="background:linear-gradient(180deg,#6a9ad0,#d9d0c0)"></div><div class="txt"><time>4 May, 2018</time><p>Duis ornare erat eget magna dapibus, in accumsan quam pharetra.</p></div></div>
  <div class="side-item" style="top:362px"><div class="photo" role="img" aria-label="Painted icon of a saint on gold" style="background:linear-gradient(135deg,#c9a03a,#6a4a1a)"></div><div class="txt"><time>4 May, 2018</time><p>Duis ornare erat eget magna dapibus, in accumsan quam pharetra.</p></div></div>
  <a class="abs btn-light" style="top:485px;left:81px">View More</a>
</section>

<!-- About -->
<section class="abs panel" style="top:1783px;left:823px;width:244px;height:405px">
  <svg class="panel-top" width="244" height="28" viewBox="0 0 244 28"><polygon points="0,14 244,0 244,12 0,26" fill="var(--orange)"/><polygon points="0,26 244,12 244,28 0,28" fill="var(--green)"/></svg>
  <h2 style="padding-top:10px">About Us</h2>
  <div class="abs" style="top:46px;left:12px;width:220px;height:296px;background:var(--card)"></div>
  <div class="abs" role="img" aria-label="Photo of two nuns in black habits" style="top:53px;left:19px;width:206px;height:110px;background:linear-gradient(135deg,#d8d8d8,#2a2a2a 55%,#c0c0c0)"></div>
  <p class="abs" style="top:170px;left:19px;width:206px;font-size:9px;line-height:13.5px;color:var(--muted)">Aliquam erat volutpat. Quisque aliquet ex nec est vestibulum pulvinar. Pellentesque convallis molestie enim sit amet efficitur. Etiam id imperdiet lectus. Vivamus lacus justo, ultrices nec erat in, euismod iaculis mauris. Vivamus eleifend vitae nulla vel malesuada. In ac malesuada lacus, et consectetur ante. Fusce vitae lectus sit amet mi pulvinar maximus. Aenean placerat, nibh vel accumsan aliquet, magna nibh accumsan nibh</p>
  <a class="abs btn-light" style="top:361px;left:80px">Read More</a>
</section>

<!-- Gallery -->
<div class="abs gallery-title">
  <span class="gallery-nav"><svg width="8" height="12" viewBox="0 0 8 12"><polyline points="6,1 2,6 6,11" fill="none" stroke="#777" stroke-width="1.5"/></svg></span>
  <span>Gallery</span>
  <span class="gallery-nav"><svg width="8" height="12" viewBox="0 0 8 12"><polyline points="2,1 6,6 2,11" fill="none" stroke="#777" stroke-width="1.5"/></svg></span>
</div>
<div class="abs gallery">
  <div role="img" aria-label="Photo of a priest in dark vestments" style="background:linear-gradient(135deg,#c28a4a,#3a2a3a 60%,#1a1a2a)"></div>
  <div role="img" aria-label="Photo of clergy in red at a service" style="background:linear-gradient(135deg,#d9b090,#a03a2a 55%,#6a5a4a)"></div>
  <div role="img" aria-label="Photo of a crowded church interior" style="background:linear-gradient(135deg,#caa060,#5a3a20 60%,#2a1a10)"></div>
  <div role="img" aria-label="Photo of flowers laid before a church" style="background:linear-gradient(135deg,#8a9aa0,#c06a7a 55%,#4a5a3a)"></div>
  <div role="img" aria-label="Black and white photo of people reading" style="background:linear-gradient(135deg,#e0e0e0,#5a5a5a 55%,#bcbcbc)"></div>
</div>

<!-- Footer -->
<footer class="abs footer">
  <svg class="abs" style="left:0;top:-6px" width="1200" height="22" viewBox="0 0 1200 22"><polygon points="0,6 1200,0 1200,12 0,16" fill="var(--orange)"/></svg>
  <h2>NEWSLETTER SUBSCRIBE</h2>
  <div class="rule" style="top:117px"></div>
  <div class="subscribe">Email Address
    <svg width="20" height="15" viewBox="0 0 20 15"><rect width="20" height="15" rx="1" fill="var(--green)"/><polyline points="1,1 10,8 19,1" fill="none" stroke="#fff" stroke-width="1.6"/></svg>
  </div>

  <div class="fcol" style="left:133px">
    <h3>Menu</h3>
    <div style="display:flex;gap:44px">
      <ul><li>Home</li><li>About Us</li><li>Evetns</li><li>Media</li><li>Community</li></ul>
      <ul><li>Forum</li><li>Support</li><li>Seminars</li><li>Newsletter</li><li>Search</li></ul>
    </div>
  </div>
  <div class="fcol" style="left:380px">
    <h3>Information</h3>
    <div style="display:flex;gap:38px">
      <ul><li>Maecenas vel</li><li>Fusce sollicitudin</li><li>Proin placerat</li><li>Pellentesque</li><li>Contact Us</li></ul>
      <ul><li>Terms and conditions of use</li><li>About us</li><li>Sitemap</li></ul>
    </div>
  </div>
  <div class="fcol" style="left:721px">
    <h3>More Links</h3>
    <ul><li>Proin a dolor</li><li>Vestibulum</li><li>Curabitur</li><li>Fusce nec</li></ul>
  </div>
  <div class="fcol" style="left:866px">
    <h3>Contact Us</h3>
    <ul><li>hello@stillwatermonastery.org</li></ul>
    <div class="social">
      <span style="background:#3b5998"></span><span style="background:#1da1f2"></span><span style="background:#dd4b39"></span><span style="background:#cb2027"></span><span style="background:#f57d00"></span><span style="background:#e52d27"></span>
    </div>
  </div>

  <div class="rule" style="top:326px"></div>
</footer>
<p class="copyright">Copyright &nbsp;©&nbsp; 2018 &nbsp;Orthodox Christian Monastery. &nbsp; All rights reserved.</p>

</body>
</html>
```